Superfood Organic Powder needs a new Standup Pouch Design

Superfood brand needs a new package design Standup pouch

We need a new packaging design
*Standup Pouch*
for a NEW superfood product to our brand PureLeafy.

This product is a superfood blend of organic powders such as spiralina, chlorella, wheatgrass etc.

The design should be modern with an organic look, - but feel free to play around with it as you wish.

Our first or *older* product is called Vital Blendo, and contains superfood powders like Maca, Moringa, Baobab, Spirulina, Chlorella, Wheatgrass

Find measurements for the standup pouch in the attachments.

We can either go with a

a white standup pouch with a slight opacity to it
(see attached sample I have from my supplier)

or

mat white standup pouch

Or Natural Kraft if

The white pouch with a slight opacity to it so you can see the powder through the pouch. One cool thing about this one is that if we have an area in the design with no colors, not even white, that area will be completely transparent, see picture of the sample pouch we have in the attachments.
In the sample photo the spider is completely transparent.

The Mat white pouch is just a basic white standup pouch with a mat finish.
What ever you think is best for your design you can suggest.

In the future we will create multiple products, each product should have its own color style to distinguish between them - this product should use green Color code as one of the green colors used in the logo. Of course not all colors should have that code, but just the identifier for this product. Please present an idea to showcase this identifier, it could be a thick horizontal or vertical line somewhere on the pouch.

The standup pouch will be digitally printed so we can use all areas of the pouch.

Please provide 3D mockup of the design in order to better get an idea of the design.
Remember that I consider you as the expert so I'm very open to any suggestions regarding this design - in the end the main goal is to attract customers and that is your area of expertise.

Please let me know if you have any questions - thanks in advance

I'm looking forward to working with you.

Here are some links I have found that I think is great designs just to give a little insight to my designs wishes.:

https://www.pinboardly.example/pin/100000000000000001/ https://www.verdanthusk.example/collections/all-superfood-products
https://www.pinboardly.example/pin/100000000000000002/
https://designduel.example/product-label-design/contests/print-design-stand-up-resealable-pouch-organic-spice-100003
https://www.pinboardly.example/pin/100000000000000004/
https://www.pinboardly.example/pin/10000000000000005/
https://www.pinboardly.example/pin/100000000000000006/
https://www.pinboardly.example/pin/100000000000000007/ https://www.pinboardly.example/pin/100000000000000008/
https://www.pinboardly.example/pin/10000000000000009/

Reason: Needed more work because I changed manufacturer of standup pouches.

Target Market(s)

Vegans, Organic interested clients, healthy living, Fitness, Juicers

Industry/Entity Type

Health And Wellness

Requirements
Must have
• The following text should be added on front of the label under the product name:
• Danish certified organic
• Superfood blend
• —
• The product contains the following ingredients and should be mentioned on the front - only the ingredients names:
• Maca, Moringa, Baobab, Spirulina, Chlorella, Wheatgrass
• —
• Organic logo:
• Organic EU logo should be present on the back (find logo in the attachments) To the right of the logo the following text is mandatory with Myriad Pro Regular as a type-font: See previous design for instructions.
• "EU-LOGO-HERE"
• DK-ØKO-000
• EU/ikke-EU-jordbrug
• EU/non-EU Agriculture
• Next to the EU organic logo we will place the danish organic logo which is attached as well, you can decide if it should be on the left or right side, it is a red Ø logo ( find in the attachments as well.
• —
• The label should contain a Nutritional Information with the danish language as primary. By law in Denmark the language used should be danish but it is allowed to add the English word after the danish separated by a /
• So it should be titled as Næringsindhold / Nutritional information (Title Bold font)
• And contain the following:
• energi (KJ/kcal)
• • fedt / fat (g)
• • - heraf mættede fedtsyrer / from saturated fat (g)
• • kulhydrat / carbohydrates (g)
• • - heraf sukkerarter / from sugar (g)
• • protein (g)
• • salt (g)
• • kostfibre / dietary fiber (g)
• —
• We need ingredients list on the back as well titled Ingredienser / Ingredients (Title Bold font)
• Maca, Moringa, Baobab, Spirulina, Chlorella, Hvedegræs / Wheatgrass
• Nettovægt / Netto weight 225 gr
• —-
• You can add some cool logos indicating that the product is:
• 100 % organic
• 100% vegan
• No additives
• Non-GMO
• Gluten free
• —
• Instructions (Title Bold font)
• Mix the superfood powder into 250 ml water with a twist of lemon, coconut water, green juice, smoothies, almond milk, or add to your favorit morning meal.
• Serving size 1-2 teaspoon
• Would be great with 3-4 images describing the instructions
• Image 1 could be fruit being put in a blender
• Image 2 could be 1 teaspoon with powder on top of a blender
• Image 3 could be a blender in use
• Image 4 poring the smoothie in to a glass to enjoy
• —
• Opbevaring / Storage (Title Bold font)
• Opbevares tørt og ikke for varmt
• Keep in a cool and dry place away from sunlight
• —
• Batch: (Title Bold font)
• Best before / Bedst før: (Title Bold font)
• —
• Barcode field
• Make room for a barcode
• —
• Produced in EU for: (Title Bold font)
• Kornvik IVS
• Tranebærvej 42
• 8960 Randers SØ
• Denmark
• www.pureleafy-shop.example (make this bold as well)
• —
• Follow us (Title Bold font)
• Instagram and facebook logo on the back with hashtag #pureleafyshop
• —
• Other than that pureleafy logo can be added as well, it is attached as well.
• I will attach our logo with original AI files.
• —
• Our mission (text)
• We want to provide our customers with the best possible superfood blends. Allowing our customers to get a product packed with antioxidants, vitamins and minerals to elevate their health to the next level. All our products are vegan friendly and GMO free - produced under the best possible circumstances.
• —
Nice to have
• Green color from the logo can be used to get it streamlined.
• Color code c2ce48

```html
<!DOCTYPE html>
<html lang="en">
<head>
<meta charset="utf-8">
<title>PureLeafy – Vital Blendo Standup Pouch</title>
<link rel="stylesheet" href="https://fonts.googleapis.com/css2?family=Questrial&family=Kaushan+Script&family=Roboto:wght@400&display=swap">
<style>
  :root {
    --backdrop: #e6e6e6;
    --pouch-white: #f7f7f7;
    --pouch-shade: #ebebeb;
    --seam: #dcdcdc;
    --lime: #c2ce48;
    --lime-soft: #cfdb5c;
    --logo-green: #4cb050;
    --olive: #8c9a3c;
    --ink: #4a4a4a;
    --grey-text: #6a6a6a;
  }
  * { box-sizing: border-box; margin: 0; padding: 0; }
  html, body {
    width: 1200px;
    height: 1200px;
    overflow: hidden;
    background: var(--backdrop);
  }
  .canvas {
    position: relative;
    width: 1200px;
    height: 1200px;
    font-family: "Questrial", "Century Gothic", sans-serif;
  }
  .pouch {
    position: absolute;
    left: 304px;
    top: 94px;
    width: 618px;
    height: 1018px;
    background: radial-gradient(circle at 50% 45%, var(--pouch-white) 0%, var(--pouch-shade) 100%);
    overflow: hidden;
  }
  .pouch__seam {
    position: absolute;
    top: 0;
    bottom: 0;
    width: 22px;
    background: var(--seam);
  }
  .pouch__seam--left { left: 0; }
  .pouch__seam--right { right: 0; }
  .identifier-band {
    position: absolute;
    left: 0;
    top: 0;
    width: 618px;
    height: 110px;
  }
  .tear-line {
    position: absolute;
    left: 0;
    right: 0;
    top: 133px;
    border-top: 1px dashed #8a8a8a;
  }
  .tear-line__label {
    position: absolute;
    top: 3px;
    font-family: "Roboto", Arial, sans-serif;
    font-size: 8px;
    color: #6a6a6a;
  }
  .tear-line__label--left { left: 54px; }
  .tear-line__label--right { right: 20px; }
  .tear-line__scissor {
    position: absolute;
    left: 18px;
    top: -7px;
  }
  .brand {
    position: absolute;
    left: 304px;
    width: 618px;
    top: 362px;
    text-align: center;
  }
  .brand__name {
    font-size: 48px;
    letter-spacing: 2px;
    color: var(--logo-green);
    line-height: 1;
  }
  .brand__hashtag {
    margin-top: 48px;
    font-size: 14px;
    letter-spacing: 2px;
    color: var(--grey-text);
  }
  .product-name {
    position: absolute;
    left: 360px;
    top: 480px;
    width: 520px;
    height: 250px;
    font-family: "Kaushan Script", cursive;
    color: var(--lime-soft);
    line-height: 1;
  }
  .product-name__line {
    position: absolute;
    white-space: nowrap;
  }
  .product-name__line--first {
    left: 120px;
    top: 0;
    font-size: 128px;
    transform: rotate(-5deg);
  }
  .product-name__line--second {
    left: 10px;
    top: 112px;
    font-size: 118px;
    transform: rotate(-5deg);
  }
  .product-name__roundel {
    position: absolute;
    left: 788px;
    top: 628px;
    width: 74px;
    height: 74px;
    border-radius: 50%;
    background: var(--lime-soft);
  }
  .claim-banner {
    position: absolute;
    left: 430px;
    top: 708px;
    width: 376px;
    height: 62px;
  }
  .claim-banner__text {
    position: absolute;
    inset: 0;
    display: flex;
    align-items: center;
    justify-content: center;
    font-size: 21px;
    letter-spacing: 1px;
    color: #ffffff;
    transform: rotate(-4deg);
  }
  .ingredients {
    position: absolute;
    left: 304px;
    width: 648px;
    top: 840px;
    text-align: center;
    font-size: 19px;
    line-height: 25px;
    color: var(--olive);
    letter-spacing: 0.3px;
  }
  .badges {
    position: absolute;
    left: 432px;
    top: 920px;
    display: flex;
    gap: 4px;
  }
  .badge {
    width: 76px;
    text-align: center;
  }
  .badge__seal {
    width: 64px;
    height: 64px;
    margin: 0 auto;
    display: block;
  }
  .badge__label {
    margin-top: 10px;
    font-size: 8.5px;
    color: var(--ink);
    white-space: nowrap;
  }
  .net-weight {
    position: absolute;
    left: 304px;
    width: 618px;
    top: 1030px;
    text-align: center;
    font-size: 18px;
    letter-spacing: 1px;
    color: var(--olive);
  }
</style>
</head>
<body>
<main class="canvas">
  <section class="pouch">
    <div class="pouch__seam pouch__seam--left"></div>
    <div class="pouch__seam pouch__seam--right"></div>

    <svg class="identifier-band" viewBox="0 0 618 110" preserveAspectRatio="none" aria-hidden="true">
      <path d="M0 0 H618 V88 L580 90 L540 86 L480 94 L420 90 L360 98 L300 94 L240 102 L180 98 L120 104 L60 102 L30 110 L0 108 Z" fill="var(--lime)"/>
    </svg>

    <div class="tear-line">
      <svg class="tear-line__scissor" width="22" height="14" viewBox="0 0 22 14" aria-hidden="true">
        <circle cx="4" cy="3.5" r="2.5" fill="none" stroke="#555" stroke-width="1.2"/>
        <circle cx="4" cy="10.5" r="2.5" fill="none" stroke="#555" stroke-width="1.2"/>
        <path d="M6 4.5 L21 11 M6 9.5 L21 3" stroke="#555" stroke-width="1.2"/>
      </svg>
      <span class="tear-line__label tear-line__label--left">Tear To Open</span>
      <span class="tear-line__label tear-line__label--right">Tear To Open</span>
    </div>
  </section>

  <header class="brand">
    <div class="brand__name">PureLeafy</div>
    <div class="brand__hashtag">#PURELEAFY</div>
  </header>

  <h1 class="product-name" aria-label="Vital Blendo">
    <span class="product-name__line product-name__line--first">Vital</span>
    <span class="product-name__line product-name__line--second">Blendo</span>
  </h1>
  <div class="product-name__roundel" aria-hidden="true"></div>

  <div class="claim-banner">
    <svg width="376" height="62" viewBox="0 0 376 62" aria-hidden="true">
      <path d="M2 40 L370 6 L374 24 L8 60 Z" fill="var(--lime)"/>
    </svg>
    <div class="claim-banner__text">DANISH CERTIFIED ORGANIC</div>
  </div>

  <p class="ingredients">MACA, MORINGA, BAOBAB, SPIRULINA,<br>CHLORELLA, WHEATGRASS</p>

  <div class="badges">
    <div class="badge">
      <svg class="badge__seal" viewBox="0 0 64 64" aria-hidden="true">
        <circle cx="32" cy="32" r="28" fill="#ffffff" stroke="var(--lime)" stroke-width="6"/>
        <text x="32" y="31" text-anchor="middle" font-family="Questrial, sans-serif" font-size="14" fill="var(--ink)">100%</text>
        <text x="32" y="42" text-anchor="middle" font-family="Questrial, sans-serif" font-size="8" fill="var(--ink)">ORGANIC</text>
      </svg>
      <div class="badge__label">100% ORGANIC</div>
    </div>
    <div class="badge">
      <svg class="badge__seal" viewBox="0 0 64 64" aria-hidden="true">
        <circle cx="32" cy="32" r="28" fill="#ffffff" stroke="var(--lime)" stroke-width="6"/>
        <text x="32" y="30" text-anchor="middle" font-family="Questrial, sans-serif" font-size="13" fill="var(--ink)">NON</text>
        <text x="32" y="44" text-anchor="middle" font-family="Questrial, sans-serif" font-size="13" fill="var(--ink)">GMO</text>
      </svg>
      <div class="badge__label">NON-GMO</div>
    </div>
    <div class="badge">
      <svg class="badge__seal" viewBox="0 0 64 64" aria-hidden="true">
        <circle cx="32" cy="32" r="28" fill="#ffffff" stroke="var(--lime)" stroke-width="6"/>
        <path d="M22 33 L29 40 L43 24" fill="none" stroke="var(--ink)" stroke-width="4" stroke-linecap="round" stroke-linejoin="round"/>
      </svg>
      <div class="badge__label">100% VEGAN</div>
    </div>
    <div class="badge">
      <svg class="badge__seal" viewBox="0 0 64 64" aria-hidden="true">
        <circle cx="32" cy="32" r="28" fill="#ffffff" stroke="var(--lime)" stroke-width="6"/>
        <path d="M14 14 L50 50" stroke="var(--lime)" stroke-width="5"/>
      </svg>
      <div class="badge__label">GULTEN FREE</div>
    </div>
    <div class="badge">
      <svg class="badge__seal" viewBox="0 0 64 64" aria-hidden="true">
        <circle cx="32" cy="32" r="28" fill="#ffffff" stroke="var(--lime)" stroke-width="6"/>
        <path d="M14 14 L50 50" stroke="var(--lime)" stroke-width="5"/>
      </svg>
      <div class="badge__label">NO PRESERVATIVE</div>
    </div>
  </div>

  <p class="net-weight">225 GM</p>
</main>
</body>
</html>
```